Food broker, trader, wholesaler, liquidator looking for a 5 pages website

Looking for a 5 pages website design. We are food brokers, traders, wholesaler and closeout buyer working with manufacturers, distributors, importers sell to retailers, food service operators and industrial (ingredients). We help market their products. We are a resource for those who need a solution in the distribution/selling/placement of food on the shelves, kitchens and pantries. Whether we open new accounts with new products or sell short dated inventory, we know where to go and get results.

Target Market(s)

Food manufacturers, food distributors, food brokers

Coding

Coded - Design and coding required

Number of Pages Required

4 page

Font styles to use
Serif

Requirements
Must have
• Food-food production-warehouse-Food packaging-people meeting-trucks-supermarket shelves-

```html
<!DOCTYPE html>
<html lang="en">
<head>
<meta charset="utf-8">
<title>Harborline Provisions</title>
<link href="https://fonts.googleapis.com/css2?family=Lato:wght@400;700;900&display=swap" rel="stylesheet">
<style>
:root{
  --navy:#0c0c52;
  --orange:#f08a2c;
  --grey-circle:#e2e2e2;
  --card:#f3f3f3;
  --text:#222;
  --footer:#222222;
  --footer-bottom:#121212;
  --white:#fff;
}
*{margin:0;padding:0;box-sizing:border-box}
html,body{width:1200px;height:3400px;overflow:hidden;background:var(--white);font-family:'Lato',sans-serif;color:var(--text)}
.page{position:relative;width:1200px;height:3400px}
.abs{position:absolute}

/* header */
.topline{left:0;top:0;width:1200px;height:5px;background:#222}
.brand{left:77px;top:26px;width:190px;text-align:center}
.brand-mark{width:100px;height:76px;border-radius:50%;background:var(--navy);margin:0 auto 10px}
.brand-name{font-weight:900;font-size:13px;color:var(--navy);letter-spacing:.3px;text-transform:uppercase}
.phone{right:74px;top:28px;display:flex;align-items:center;gap:8px;font-weight:900;font-size:23px;color:var(--navy)}
.phone-ico{width:30px;height:30px;border-radius:50%;background:#bbb;display:flex;align-items:center;justify-content:center}
.nav{right:74px;top:88px;display:flex;align-items:center}
.nav a{font-size:15px;font-weight:700;color:#111;text-decoration:none;padding:9px 21px;border-radius:20px}
.nav a.active{background:var(--navy);color:#fff}

/* hero */
.hero{left:0;top:145px;width:1200px;height:609px;
  background:
    linear-gradient(rgba(0,0,0,.18),rgba(0,0,0,.28)),
    radial-gradient(ellipse 230px 190px at 250px 300px,rgba(170,200,205,.75),rgba(170,200,205,0)),
    radial-gradient(ellipse 180px 200px at 560px 250px,rgba(120,86,64,.75),rgba(120,86,64,0)),
    radial-gradient(ellipse 230px 330px at 1010px 430px,rgba(232,236,240,.95),rgba(232,236,240,0)),
    radial-gradient(ellipse 150px 170px at 980px 210px,rgba(196,160,134,.8),rgba(196,160,134,0)),
    radial-gradient(ellipse 360px 140px at 420px 560px,rgba(25,25,28,.9),rgba(25,25,28,0)),
    linear-gradient(100deg,#2c3236 0%,#3d4346 40%,#4b4d4e 65%,#6a6866 100%)}
.hero-title{left:0;top:385px;width:1200px;text-align:center;color:#fff;font-weight:900;line-height:1;text-shadow:0 2px 10px rgba(0,0,0,.35)}
.hero-title .l1{font-size:58px;display:block}
.hero-title .l2{font-size:66px;display:block;margin-top:6px}
.dots{left:560px;top:702px;display:flex;gap:10px}
.dots span{width:12px;height:12px;border-radius:50%;background:#111}
.dots span.on{background:#fff}

/* what we do */
.section-title{width:1200px;left:0;text-align:center;font-weight:900;font-size:33px;color:var(--navy)}
.card{top:956px;width:330px;height:280px;background:var(--card);border-radius:8px;text-align:center}
.card-ico{position:absolute;left:90px;top:-54px;width:150px;height:108px;border-radius:50%;background:var(--navy);display:flex;align-items:center;justify-content:center}
.card h3{margin-top:86px;font-size:22px;font-weight:700;color:var(--navy)}
.card p{margin:12px auto 0;width:260px;font-size:14.5px;line-height:28px;color:#333}
.btn-outline{position:absolute;left:83px;top:207px;width:164px;height:43px;border:2px solid #555;border-radius:22px;font-size:14.5px;font-weight:700;color:var(--navy);display:flex;align-items:center;justify-content:center;background:#fff}

/* about */
.about{left:0;top:1305px;width:1200px;height:439px;background:var(--navy);overflow:hidden}
.band-photo{position:absolute;top:0;height:100%}
.about-photo{left:585px;width:615px;clip-path:path('M154 0H615V439H24C-10 300 35 120 154 0Z');
  background:
    radial-gradient(ellipse 120px 90px at 220px 160px,rgba(255,255,255,.9),rgba(255,255,255,0)),
    radial-gradient(ellipse 110px 130px at 400px 130px,rgba(176,128,100,.7),rgba(176,128,100,0)),
    radial-gradient(ellipse 120px 110px at 540px 110px,rgba(60,48,40,.6),rgba(60,48,40,0)),
    radial-gradient(ellipse 200px 150px at 430px 330px,rgba(236,240,246,.95),rgba(236,240,246,0)),
    radial-gradient(ellipse 140px 200px at 80px 300px,rgba(150,160,175,.8),rgba(150,160,175,0)),
    linear-gradient(135deg,#e6ecf1,#b7c2cc 55%,#6f7a86)}
.about h2{position:absolute;left:75px;top:60px;color:#fff;font-size:33px;font-weight:900}
.about .copy{position:absolute;left:75px;top:117px;width:475px;color:#fff;font-size:14.5px;line-height:26px}
.about .copy p+p{margin-top:4px}
.btn-white{position:absolute;height:45px;border-radius:23px;background:#fff;color:var(--navy);font-weight:700;font-size:15px;display:flex;align-items:center;justify-content:center}

/* process */
.node{position:absolute;width:169px;height:169px;border-radius:50%;background:var(--grey-circle);border:3px solid #fff;display:flex;flex-direction:column;align-items:center;justify-content:center;text-align:center;color:var(--navy);font-weight:900;font-size:19px;line-height:23px}
.node.hot{background:var(--orange);color:#fff;box-shadow:0 0 0 3px #ddd}
.node svg{margin-bottom:6px}
.core{position:absolute;left:510px;top:2170px;width:192px;text-align:center}
.core .dot{width:100px;height:74px;border-radius:50%;background:var(--navy);margin:0 auto 12px}
.core .name{font-weight:900;font-size:14px;color:var(--navy);text-transform:uppercase}

/* contact */
.contact{left:0;top:2602px;width:1200px;height:438px;background:var(--navy);overflow:hidden}
.contact-photo{left:0;width:615px;clip-path:path('M0 0H460C590 130 640 300 610 438H0Z');
  background:
    radial-gradient(ellipse 150px 120px at 320px 200px,rgba(230,220,90,.75),rgba(230,220,90,0)),
    radial-gradient(ellipse 110px 150px at 450px 250px,rgba(170,196,228,.9),rgba(170,196,228,0)),
    radial-gradient(ellipse 90px 80px at 470px 120px,rgba(170,80,50,.7),rgba(170,80,50,0)),
    radial-gradient(ellipse 160px 110px at 130px 250px,rgba(205,210,215,.85),rgba(205,210,215,0)),
    radial-gradient(ellipse 260px 180px at 130px 80px,rgba(190,150,110,.85),rgba(190,150,110,0)),
    linear-gradient(135deg,#a8896a,#7d7064 50%,#b9bcc2)}
.contact h2{position:absolute;left:660px;top:64px;color:#fff;font-size:33px;font-weight:900}
.field{position:absolute;background:#fff;border-radius:22px;font-size:14.5px;color:#333;padding:14px 20px}

/* footer */
.footer{left:0;top:3040px;width:1200px;height:275px;background:var(--footer);color:#fff}
.footer h4{position:absolute;top:65px;font-size:20px;font-weight:900;text-transform:uppercase}
.footer .col{position:absolute;top:108px;font-size:14.5px;line-height:32px}
.footer .col.text{line-height:28px;width:315px}
.links{position:absolute;left:915px;top:112px;display:flex;gap:16px}
.links svg{display:block}
.bottom{left:0;top:3315px;width:1200px;height:85px;background:var(--footer-bottom);color:#fff;font-size:13.5px;text-align:center;padding-top:38px}
</style>
</head>
<body>
<div class="page">

  <div class="abs topline"></div>
  <div class="abs brand">
    <div class="brand-mark"></div>
    <div class="brand-name">Harborline Provisions</div>
  </div>
  <div class="abs phone">
    <span class="phone-ico"><svg width="16" height="16" viewBox="0 0 24 24"><path fill="#0c0c52" d="M6.6 10.8a15 15 0 0 0 6.6 6.6l2.2-2.2a1 1 0 0 1 1-.25 11.4 11.4 0 0 0 3.6.57 1 1 0 0 1 1 1V20a1 1 0 0 1-1 1A17 17 0 0 1 3 4a1 1 0 0 1 1-1h3.5a1 1 0 0 1 1 1c0 1.25.2 2.45.57 3.57a1 1 0 0 1-.25 1z"/></svg></span>
    1-800-555-0142
  </div>
  <nav class="abs nav">
    <a class="active">HOME</a><a>ABOUT US</a><a>WHAT WE DO</a><a>CONTACT</a><a>GIVING BACK</a>
  </nav>

  <div class="abs hero" role="img" aria-label="Photo of two traders studying market charts on a computer screen"></div>
  <h1 class="abs hero-title"><span class="l1">WELCOME TO</span><span class="l2">HARBORLINE PROVISIONS</span></h1>
  <div class="abs dots"><span class="on"></span><span></span><span></span><span></span></div>

  <h2 class="abs section-title" style="top:822px">WHAT WE DO</h2>

  <div class="abs card" style="left:75px">
    <div class="card-ico"><svg width="62" height="62" viewBox="0 0 62 62" fill="none" stroke="#fff" stroke-width="2.5"><rect x="8" y="26" width="36" height="26"/><path d="M14 44l8-9 6 5 10-12"/><circle cx="46" cy="16" r="8"/><path d="M43 19l6-6"/><rect x="40" y="34" width="16" height="18"/><path d="M4 56h54"/></svg></div>
    <h3>Sales &amp; Marketing</h3>
    <p>We connect food buyers and sellers through a dedicated approach.</p>
    <div class="btn-outline">READ MORE</div>
  </div>
  <div class="abs card" style="left:436px">
    <div class="card-ico"><svg width="66" height="56" viewBox="0 0 66 56" fill="none" stroke="#fff" stroke-width="2.5"><rect x="8" y="4" width="50" height="36" rx="2"/><path d="M2 46h62l-4 6H6z"/><path d="M14 32l10-10 8 6 14-14"/><path d="M14 36v-4M22 36v-8M30 36v-6M38 36v-10M46 36v-14"/></svg></div>
    <h3>Trading</h3>
    <p style="width:280px">We purchase goods anywhere and ship them Nationwide and Export</p>
    <div class="btn-outline">READ MORE</div>
  </div>
  <div class="abs card" style="left:796px">
    <div class="card-ico"><svg width="60" height="60" viewBox="0 0 60 60" fill="none" stroke="#fff" stroke-width="2.5"><rect x="6" y="4" width="22" height="18"/><rect x="32" y="4" width="22" height="18"/><rect x="34" y="34" width="22" height="18"/><circle cx="18" cy="32" r="6"/><path d="M6 56c0-9 5-14 12-14s12 5 12 14"/></svg></div>
    <h3>Closeout/Excess Inventory</h3>
    <p style="width:300px">We buy closeouts and excess inventory for prisons, outlet stores and discounters.</p>
    <div class="btn-outline">READ MORE</div>
  </div>

  <section class="abs about">
    <div class="band-photo about-photo" role="img" aria-label="Photo of two colleagues reviewing figures on a monitor in an office"></div>
    <h2>ABOUT US</h2>
    <div class="copy">
      <p>Harborline Provisions works with food manufacturers, brand owners, distributors and wholesalers market their products. Retail, Food Service and Industrial ingredients.</p>
      <p>Founded in 2008, Harborline Provisions started with the distribution of gluten free products understanding the need to provide access to unique flavors and products forthe celiac consumers. From this, we expanded into deli, dairy, groceries, frozen and beverages.</p>
    </div>
    <div class="btn-white" style="left:75px;top:329px;width:165px">READ MORE</div>
  </section>

  <h2 class="abs section-title" style="top:1809px">PROCESS CYCLE</h2>

  <svg class="abs" style="left:0;top:1800px" width="1200" height="760" viewBox="0 1800 1200 760" fill="none">
    <circle cx="606" cy="2231" r="254" stroke="#333" stroke-width="1.5"/>
    <circle cx="606" cy="2231" r="115" stroke="#333" stroke-width="1.5"/>
    <g stroke="#333" stroke-width="1.5">
      <path d="M560 2115l8 4-6 7"/><path d="M648 2116l8 5-8 4"/><path d="M712 2180l1 9-8-3"/>
      <path d="M700 2303l-3 8-5-7"/><path d="M614 2346l-8 4 7 5"/><path d="M520 2305l-7 1 4 8"/><path d="M490 2196l3-8 4 7"/>
    </g>
  </svg>

  <div class="node" style="left:521px;top:1892px"><svg width="56" height="48" viewBox="0 0 56 48" fill="none" stroke="#222" stroke-width="2"><rect x="4" y="6" width="10" height="20"/><circle cx="24" cy="34" r="10"/><circle cx="40" cy="32" r="8"/><path d="M2 44h52"/></svg>FOOD</div>
  <div class="node" style="left:712px;top:1985px"><svg width="56" height="40" viewBox="0 0 56 40" fill="none" stroke="#222" stroke-width="2"><circle cx="12" cy="18" r="5"/><circle cx="28" cy="18" r="5"/><circle cx="44" cy="18" r="5"/><rect x="2" y="26" width="52" height="8" rx="4"/><path d="M6 6h20M32 6h12"/></svg>FOOD<br>PRODUCTION</div>
  <div class="node" style="left:760px;top:2193px"><svg width="54" height="52" viewBox="0 0 54 52" fill="none" stroke="#222" stroke-width="2"><path d="M4 18L27 4l23 14v30H4z"/><rect x="12" y="24" width="30" height="24"/><rect x="28" y="34" width="10" height="10"/></svg>WAREHOUSE</div>
  <div class="node" style="left:628px;top:2360px"><svg width="40" height="54" viewBox="0 0 40 54" fill="none" stroke="#222" stroke-width="2"><rect x="4" y="10" width="32" height="42" rx="2"/><path d="M8 2h24v8H8z"/><circle cx="20" cy="32" r="8"/></svg>FOOD<br>PACKAGING</div>
  <div class="node" style="left:413px;top:2360px"><svg width="54" height="48" viewBox="0 0 54 48" fill="none" stroke="#222" stroke-width="2"><rect x="6" y="4" width="14" height="10"/><rect x="32" y="2" width="14" height="10"/><circle cx="12" cy="24" r="5"/><circle cx="27" cy="24" r="5"/><circle cx="42" cy="24" r="5"/><path d="M2 36h50v10M6 36v10"/></svg>PEOPLE<br>MEETING</div>
  <div class="node" style="left:281px;top:2193px"><svg width="70" height="46" viewBox="0 0 70 46" fill="none" stroke="#222" stroke-width="2"><rect x="4" y="4" width="40" height="30"/><path d="M44 14h12l10 12v8H44z"/><circle cx="16" cy="38" r="5"/><circle cx="54" cy="38" r="5"/><path d="M16 18l6 6 12-12"/></svg>TRUCKS</div>
  <div class="node hot" style="left:328px;top:1985px"><svg width="44" height="50" viewBox="0 0 44 50" fill="none" stroke="#fff" stroke-width="2.5"><rect x="4" y="2" width="36" height="46"/><path d="M4 14h36M4 26h36M4 38h36"/><path d="M10 8h24M10 20h24M10 32h24"/></svg>SUPERMARKET<br>SHELVES</div>

  <div class="core"><div class="dot"></div><div class="name">Harborline Provisions</div></div>

  <section class="abs contact">
    <div class="band-photo contact-photo" role="img" aria-label="Photo of two warehouse workers checking stock on a laptop"></div>
    <h2>CONTACT US</h2>
    <div class="field" style="left:660px;top:127px;width:228px;height:44px;padding-top:12px">Name</div>
    <div class="field" style="left:898px;top:127px;width:228px;height:44px;padding-top:12px">Email Address</div>
    <div class="field" style="left:659px;top:185px;width:467px;height:121px">Message</div>
    <div class="btn-white" style="left:660px;top:326px;width:165px;height:44px">SUBMIT NOW</div>
  </section>

  <footer class="abs footer">
    <h4 style="left:75px">About Us</h4>
    <div class="col text" style="left:75px">Lorem ipsum dolor sit amet, consectetur adipiscing elit. Donec euismod magna quis laoreet rhoncus. Morbi eleifend, ante at tincidunt rutrum, nulla felis sodales sem, non molestie nulla nibh vitae est.</div>
    <h4 style="left:452px">Site Map</h4>
    <div class="col" style="left:452px">About Us<br>What we do<br>Contact<br>Giving Back</div>
    <h4 style="left:653px">What We Do</h4>
    <div class="col" style="left:653px">Sales &amp; Marketing<br>Trading<br>Closeout/Excess Inventory</div>
    <h4 style="left:915px">Follow Us</h4>
    <div class="links" aria-label="Contact links">
      <svg width="20" height="20" viewBox="0 0 24 24" fill="none" stroke="#fff" stroke-width="2"><rect x="2" y="5" width="20" height="14" rx="2"/><path d="M2 7l10 7 10-7"/></svg>
      <svg width="20" height="20" viewBox="0 0 24 24" fill="#fff"><path d="M6.6 10.8a15 15 0 0 0 6.6 6.6l2.2-2.2a1 1 0 0 1 1-.25 11.4 11.4 0 0 0 3.6.57 1 1 0 0 1 1 1V20a1 1 0 0 1-1 1A17 17 0 0 1 3 4a1 1 0 0 1 1-1h3.5a1 1 0 0 1 1 1c0 1.25.2 2.45.57 3.57a1 1 0 0 1-.25 1z"/></svg>
      <svg width="20" height="20" viewBox="0 0 24 24" fill="none" stroke="#fff" stroke-width="2"><path d="M12 22s7-7 7-12a7 7 0 0 0-14 0c0 5 7 12 7 12z"/><circle cx="12" cy="10" r="2.5"/></svg>
      <svg width="20" height="20" viewBox="0 0 24 24" fill="none" stroke="#fff" stroke-width="2"><path d="M3 4h18v12H9l-5 4V4z"/></svg>
      <svg width="20" height="20" viewBox="0 0 24 24" fill="none" stroke="#fff" stroke-width="2"><circle cx="12" cy="12" r="10"/><path d="M2 12h20M12 2c3 3 3 17 0 20M12 2c-3 3-3 17 0 20"/></svg>
    </div>
  </footer>
  <div class="abs bottom">Copyright © 2020. Company Name All rights reserved.</div>

</div>
</body>
</html>
```